eBook Cover_H. Lindqvist-Borna
Schnell und zuverlässoig,Änderungswünsche wurden umgehend ausgeführt. Vielen Dank für das tolle Cover zu meinem ersten Buch!
Zielgruppe
freie Roman-Autorin (Erstlingswerk)
Zielgruppe: Lesende (Erwachsene), Frauen
Charakterisierung: magisch-realistischer Familienroman, spielt im Europa der Jetzt-Zeit
Aufgabenstellung
Im ersten Schritt geht es um ein Cover für ein eBook, das aber bei Bedarf als Book on Demand gedruckt werden soll. Es wird daher später Anforderung bzgl. Dicke / Umfang des gedruckten Buches und einer Rückseite geben. Das gewählte Design soll dann dahingehend überarbeitet und finale Druckdaten zur Verfügung gestellt werden. Dies soll von vornherein berücksichtigt werden und im Preis enthalten sein.
Titel: Regen über Glas, Monde im Moos
Autorinnenname: Henrike Lindqvist-Borna
des weiteren auf dem Cover: Roman

```html
<!DOCTYPE html>
<html lang="de">
<head>
<meta charset="utf-8">
<title>Regen über Glas, Monde im Moos – Henrike Lindqvist-Borna</title>
<link rel="stylesheet" href="https://fonts.googleapis.com/css2?family=Oswald:wght@600;700&family=Open+Sans:wght@400;500&display=swap">
<style>
  :root {
    --paper: #ffffff;
    --red-deep: #9e0d06;
    --red-main: #d4220d;
    --red-bright: #f2542a;
    --ink-grey: #565c63;
    --frame-grey: #4f555c;
    --white: #ffffff;
  }
  * { margin: 0; padding: 0; box-sizing: border-box; }
  html, body {
    width: 948px;
    height: 1200px;
    overflow: hidden;
    background: var(--paper);
  }
  .cover {
    position: relative;
    width: 948px;
    height: 1200px;
    background: var(--paper);
    overflow: hidden;
  }
  .cover__art {
    position: absolute;
    inset: 0;
    width: 948px;
    height: 1200px;
  }
  .cover__author {
    position: absolute;
    top: 372px;
    left: 470px;
    padding: 12px 22px;
    border: 2px solid var(--frame-grey);
    font-family: "Open Sans", Arial, sans-serif;
    font-weight: 500;
    font-size: 22px;
    letter-spacing: 1px;
    color: var(--ink-grey);
    text-transform: uppercase;
    white-space: nowrap;
  }
  .cover__title {
    position: absolute;
    top: 492px;
    right: 66px;
    font-family: "Oswald", "Arial Narrow", sans-serif;
    font-weight: 700;
    font-size: 64px;
    line-height: 1.08;
    letter-spacing: 2px;
    color: var(--ink-grey);
    text-transform: uppercase;
    text-align: right;
  }
  .cover__title span { display: block; }
  .cover__genre {
    position: absolute;
    left: 112px;
    bottom: 62px;
    font-family: "Oswald", "Arial Narrow", sans-serif;
    font-weight: 700;
    font-size: 56px;
    letter-spacing: 2px;
    color: var(--white);
    text-transform: uppercase;
  }
</style>
</head>
<body>
  <main class="cover">
    <svg class="cover__art" viewBox="0 0 948 1200" role="img" aria-label="Abstraktes rotes Wellenmuster mit geschwungenen Linien und Kreisen">
      <defs>
        <radialGradient id="redField" cx="0.55" cy="0.45" r="0.75">
          <stop offset="0" stop-color="var(--red-bright)"/>
          <stop offset="0.5" stop-color="var(--red-main)"/>
          <stop offset="1" stop-color="var(--red-deep)"/>
        </radialGradient>
      </defs>
      <polygon class="cover__red-panel" points="0,0 505,0 362,600 455,1200 0,1200" fill="url(#redField)"/>
    </svg>

    <div class="cover__author">Henrike Lindqvist-Borna</div>

    <h1 class="cover__title">
      <span>Regen über Glas</span>
      <span>Monde im Moos</span>
    </h1>

    <p class="cover__genre">Roman</p>
  </main>
</body>
</html>
```